Business Card Design

We need a business card designed for a new company based in Melbourne called Kvt solutions. Kvt solutions provides management consulting specialising in the health and social services sector.

Kvt solutions offer a unique set of specialist skills │dealing with all levels of government │ unique communication skills│intimate knowledge of the health sector │solutions tailored to unique circumstances.

Kvt solutions takes on a select number of clients at any one time, this ensures that your organisation receives the attention required. On larger projects, Kvt solutions join up with other consultants to bring specialist skills to a project.
Updates

This is the first time I have used Pixel Harbor and thank you all for responding. The variation is amazing and makes it hard to decide. I have to ask some of my friends to give me their views. The response is fantastic. The one I pick will basically be the most visually appealing

Industry/Entity Type

Management Consulting

Contact Information for Business Card

Martin Oakes, Principal, Kvt solutions, 14 Wexcombe Ave, Larkdale VIC 3189, 0417 382 914, martino@kvtsolutions-example.com.au, www.kvtsolutions-example.com.au

```html
<!DOCTYPE html>
<html lang="en">
<head>
<meta charset="utf-8">
<title>Kvt solutions – Business Card</title>
<link rel="stylesheet" href="https://fonts.googleapis.com/css2?family=Arimo:ital,wght@0,400;0,700;1,700&family=Roboto+Slab:wght@700&display=swap">
<style>
  :root {
    --backdrop: #e9e6e1;
    --brand-red: #c00015;
    --pattern-red: #d5304d;
    --ink: #111111;
    --frame: #000000;
    --paper: #ffffff;
  }
  * { margin: 0; padding: 0; box-sizing: border-box; }
  html, body {
    width: 1200px; height: 798px; overflow: hidden;
    background: var(--backdrop);
  }
  .canvas { position: relative; width: 1200px; height: 798px; }

  /* Front of card */
  .card-front {
    position: absolute; left: 108px; top: 95px;
    width: 492px; height: 607px;
    background: var(--brand-red);
  }
  .pattern-band {
    position: absolute; left: 197px; width: 160px;
    background: var(--pattern-red); opacity: .55;
  }
  .pattern-band--top { top: 5px; height: 245px; }
  .pattern-band--bottom { top: 355px; height: 250px; }
  .brand {
    position: absolute; left: 90px; top: 258px; width: 348px;
    text-align: right; color: var(--paper);
  }
  .brand-name {
    font-family: "Arimo", Arial, sans-serif;
    font-weight: 700; font-size: 40px; line-height: 1;
    letter-spacing: 1px;
  }
  .brand-tagline {
    margin-top: 14px;
    font-family: "Roboto Slab", Georgia, serif;
    font-weight: 700; font-size: 11.5px; letter-spacing: .6px;
    text-transform: uppercase;
  }

  /* Back of card */
  .card-back {
    position: absolute; left: 600px; top: 95px;
    width: 493px; height: 607px;
    background: var(--frame);
  }
  .card-back__panel {
    position: absolute; left: 0; top: 46px;
    width: 446px; height: 515px;
    background: var(--paper);
  }
  .contact {
    position: absolute; right: 13px; top: 330px;
    text-align: right; color: var(--ink);
    font-family: "Arimo", Arial, sans-serif;
  }
  .contact-name {
    color: var(--brand-red); font-size: 27px; font-weight: 400;
    word-spacing: 4px; line-height: 1.2;
  }
  .contact-role {
    font-size: 23px; font-weight: 700; font-style: italic;
    line-height: 1.2; margin-bottom: 16px;
  }
  .contact-line { font-size: 17px; line-height: 22.5px; letter-spacing: .3px; }
  .contact-line svg { vertical-align: -2px; margin-right: 8px; }
  .accent { color: var(--brand-red); }
</style>
</head>
<body>
<main class="canvas">
  <section class="card-front">
    <div class="pattern-band pattern-band--top" role="img" aria-label="Decorative cross pattern band"></div>
    <div class="pattern-band pattern-band--bottom" role="img" aria-label="Decorative cross pattern band"></div>
    <div class="brand">
      <div class="brand-name">Kvt solutions</div>
      <div class="brand-tagline">Health &amp; Social Services Consulting</div>
    </div>
  </section>

  <section class="card-back">
    <div class="card-back__panel">
      <div class="contact">
        <div class="contact-name">Martin Oakes</div>
        <div class="contact-role">Principal</div>
        <div class="contact-line">14 Wexcombe Ave, Larkdale VIC 3189</div>
        <div class="contact-line">
          <svg width="8" height="14" viewBox="0 0 8 14" aria-hidden="true"><rect x="1" y="1" width="6" height="12" rx="1" fill="none" stroke="#111" stroke-width="1.2"/><rect x="2.5" y="3" width="3" height="4" fill="#111"/></svg>0417 382 914
        </div>
        <div class="contact-line">
          <svg width="18" height="12" viewBox="0 0 18 12" aria-hidden="true"><rect x="1" y="1" width="16" height="10" fill="none" stroke="#111" stroke-width="1.2"/><path d="M1 1 L9 7 L17 1" fill="none" stroke="#111" stroke-width="1.2"/></svg>martino@kvtsolutions-example.com.au
        </div>
        <div class="contact-line">www.<span class="accent">kvtsolutions-example</span>.com</div>
      </div>
    </div>
  </section>
</main>
</body>
</html>
```